Road Construction Company needs business cards

We would like a new business card designed for our business.

We're a road construction company based in Qld, Australia.

Can the business card please have the following information on it.

Name: Warren Halbeck
Position: General Manager
Phone: 0472 915 348
Email: Warren.halbeck@tovrin.com.au
Address: 87 Marrow Ave, Pendlebay, QLD, 4023
Website: www.tovrin.com.au

Visually we'd like the card to be professional and simple.

Attached is our logo.

Our website is www.tovrin.com.au

Target Market(s)

Men aged 25-60

Contact Information for Business Card

As listed in project description

Font styles to use
Serif

Requirements
Must have
• Large logo on back of card

```html
<!DOCTYPE html>
<html lang="en">
<head>
<meta charset="utf-8">
<title>Tovrin Business Card</title>
<link href="https://fonts.googleapis.com/css2?family=Exo+2:wght@400;500;800&display=swap" rel="stylesheet">
<style>
  :root {
    --backdrop: #c9c9c9;
    --blue-light: #33a6d9;
    --blue-mid: #1c7fc6;
    --blue-deep: #0a4f9f;
    --navy: #0b3d8c;
    --accent: #2a9ad8;
    --ink: #1d1d24;
    --paper: #ffffff;
    --paper-shade: #ececec;
  }
  * { margin: 0; padding: 0; box-sizing: border-box; }
  html, body {
    width: 1200px; height: 900px; overflow: hidden;
    background: var(--backdrop);
    font-family: "Exo 2", sans-serif;
  }
  .canvas { position: relative; width: 1200px; height: 900px; }
  .card {
    position: absolute; left: 290px; width: 620px; height: 354px;
    border-radius: 26px; overflow: hidden;
  }
  .card--back {
    top: 70px;
    background: linear-gradient(160deg, var(--blue-light) 0%, var(--blue-mid) 45%, var(--blue-deep) 100%);
    display: flex; align-items: center; justify-content: center;
  }
  .card--front {
    top: 476px;
    background: linear-gradient(120deg, var(--paper) 55%, var(--paper-shade) 78%, var(--paper) 100%);
  }
  .brand-name {
    font-weight: 800; letter-spacing: 6px; text-transform: uppercase; line-height: 1;
  }
  .card--back .brand-name { color: var(--paper); font-size: 78px; }
  .card--front .brand-name {
    position: absolute; left: 44px; top: 46px;
    color: var(--navy); font-size: 58px;
  }
  .holder { position: absolute; left: 44px; top: 168px; }
  .holder-name { color: var(--navy); font-weight: 800; font-size: 27px; text-transform: uppercase; letter-spacing: 0.5px; }
  .holder-role { color: var(--accent); font-weight: 400; font-size: 21px; margin-top: 2px; }
  .contacts { position: absolute; left: 44px; top: 254px; list-style: none; }
  .contacts li {
    display: flex; align-items: center; gap: 10px;
    color: var(--ink); font-size: 18px; line-height: 27px;
  }
  .contacts svg { width: 17px; height: 17px; flex: none; }
  .contacts .site-domain { color: var(--navy); }
  .address {
    position: absolute; right: 44px; top: 160px; text-align: right;
    color: var(--ink); font-size: 18px; line-height: 26px;
  }
</style>
</head>
<body>
<main class="canvas">
  <section class="card card--back" aria-label="Card back">
    <span class="brand-name">Tovrin</span>
  </section>

  <section class="card card--front" aria-label="Card front">
    <span class="brand-name">Tovrin</span>

    <div class="holder">
      <p class="holder-name">Warren Halbeck</p>
      <p class="holder-role">General Manager</p>
    </div>

    <ul class="contacts">
      <li>
        <svg viewBox="0 0 24 24" aria-hidden="true"><path fill="#0b3d8c" d="M6.6 10.8a15.2 15.2 0 0 0 6.6 6.6l2.2-2.2a1 1 0 0 1 1-.25 11.4 11.4 0 0 0 3.6.57 1 1 0 0 1 1 1V20a1 1 0 0 1-1 1A17 17 0 0 1 3 4a1 1 0 0 1 1-1h3.5a1 1 0 0 1 1 1c0 1.25.2 2.45.57 3.6a1 1 0 0 1-.25 1z"/></svg>
        0472 915 348
      </li>
      <li>
        <svg viewBox="0 0 24 24" aria-hidden="true"><rect x="2" y="5" width="20" height="14" rx="1" fill="#0b3d8c"/><path d="M2.5 6l9.5 7 9.5-7" stroke="#fff" stroke-width="1.6" fill="none"/></svg>
        Warren.halbeck@tovrin.com.au
      </li>
      <li>
        <svg viewBox="0 0 24 24" aria-hidden="true"><g fill="none" stroke="#0b3d8c" stroke-width="2"><circle cx="12" cy="12" r="9"/><ellipse cx="12" cy="12" rx="4" ry="9"/><path d="M3 12h18M5 7h14M5 17h14"/></g></svg>
        <span>www.<span class="site-domain">tovrin</span>.com.au</span>
      </li>
    </ul>

    <address class="address" style="font-style: normal;">
      87 Marrow Ave<br>Pendlebay, QLD, 4023
    </address>
  </section>
</main>
</body>
</html>
```